50 Page Catalog Full Redesign New Look

We are looking for a redesign of our Catalog,

We are looking for a modern redesign of our Catalog, with our new logo most of the products will be the same with some new products as well.
Please use colors in the new logo attached
Attached is our current design please see this for what product will go in the catulog
Updates

Designs look the same

Target Market(s)

Automotive

Font styles to use
Other font styles liked:
• Our Font is outfit

Colors

Designer to choose colors to be used in the design.

```html
<!DOCTYPE html>
<html lang="en">
<head>
<meta charset="utf-8">
<title>Korvane Catalogue – Contents &amp; Who We Are</title>
<link href="https://fonts.googleapis.com/css2?family=Outfit:wght@300;400;500;600;700&display=swap" rel="stylesheet">
<style>
  :root {
    --navy: #123f6b;
    --blue: #1f5586;
    --blue-light: #3a76a6;
    --orange: #f0a21b;
    --orange-deep: #e38a12;
    --paper: #ffffff;
    --backdrop: #dcdcdc;
    --ink: #2a2a2a;
  }
  * { box-sizing: border-box; margin: 0; padding: 0; }
  html, body {
    width: 1200px; height: 840px; overflow: hidden;
    background: var(--backdrop);
    font-family: "Outfit", sans-serif;
  }
  .spread {
    position: absolute; left: 35px; top: 25px;
    width: 1130px; height: 790px;
    display: flex;
  }
  .page {
    position: relative; width: 565px; height: 790px;
    background: var(--paper); overflow: hidden;
  }

  /* Left page – contents */
  .contents-title {
    position: absolute; left: 60px; top: 52px;
    font-size: 34px; font-weight: 600; letter-spacing: 0.5px;
    color: var(--navy); text-transform: uppercase;
  }
  .contents-title .accent { color: var(--orange-deep); }
  .top-band {
    position: absolute; right: 0; top: 118px; width: 175px; height: 46px;
    background: linear-gradient(90deg, var(--navy), var(--blue-light));
    border-top-left-radius: 30px 46px;
  }
  .contents-list {
    position: absolute; left: 60px; top: 182px; width: 460px;
    list-style: none;
  }
  .contents-list li {
    display: flex; align-items: baseline;
    height: 27px; font-size: 13px; text-transform: uppercase;
  }
  .contents-list .pages { width: 80px; color: var(--orange-deep); font-weight: 400; }
  .contents-list .section { color: var(--navy); font-weight: 500; }
  .footer-rule {
    position: absolute; left: 40px; right: 40px; top: 725px;
    border-top: 1.5px solid var(--ink);
  }
  .footer-url {
    position: absolute; left: 0; right: 0; top: 742px; text-align: center;
    font-size: 15px; color: var(--ink); letter-spacing: 0.5px;
  }

  /* Right page – who we are */
  .backdrop-shape { position: absolute; inset: 0; }
  .value-grid {
    position: absolute; left: 22px; top: 178px;
    display: grid; grid-template-columns: 140px 140px; gap: 14px 14px;
  }
  .value-card {
    height: 140px; border: 1.5px solid var(--orange);
    border-radius: 16px; overflow: hidden;
    display: flex; flex-direction: column;
  }
  .value-card .photo { height: 62px; }
  .value-card .label { flex: 1; text-align: center; color: #fff; padding: 7px 8px 0; }
  .value-card h3 { font-size: 18px; font-weight: 500; line-height: 1.1; }
  .value-card p { font-size: 9.5px; font-weight: 300; line-height: 1.25; margin-top: 4px; }
  .photo-care { background: linear-gradient(135deg, #d9343a, #9fb3c6 60%, #5b7690); }
  .photo-speed { background: linear-gradient(135deg, #c62a2f, #7e1e26 50%, #2a3b52); }
  .photo-satisfaction { background: linear-gradient(135deg, #3b4450, #1d2430 60%, #5a6674); }
  .photo-enjoyment { background: linear-gradient(135deg, #cfe0ef, #d4363a 55%, #8c1f22); }

  .about {
    position: absolute; left: 330px; top: 150px; width: 215px; color: #fff;
  }
  .about h2 {
    color: var(--orange); font-size: 22px; font-weight: 600; line-height: 1.2; margin-bottom: 8px;
  }
  .about p {
    font-size: 9.5px; font-weight: 300; line-height: 1.4; margin-bottom: 7px;
  }
  .team-photo {
    position: absolute; left: 0; right: 0; bottom: 0; height: 290px;
    background: linear-gradient(160deg, #9fb7c9 0%, #5f7f99 40%, #23405e 100%);
    clip-path: path("M0 18 Q 280 -6 565 40 L 565 290 L 0 290 Z");
  }
</style>
</head>
<body>
  <main class="spread">
    <section class="page page-left">
      <h1 class="contents-title"><span class="accent">Table of</span> Content</h1>
      <div class="top-band"></div>
      <ol class="contents-list">
        <li><span class="pages">4-5</span><span class="section">About us &amp; our solutions</span></li>
        <li><span class="pages">6-7</span><span class="section">Number plate frames</span></li>
        <li><span class="pages">8-11</span><span class="section">Keyrings</span></li>
        <li><span class="pages">12-13</span><span class="section">Stickers, mudflaps &amp; service book wallets</span></li>
        <li><span class="pages">14-15</span><span class="section">Hand over gifts &amp; caps</span></li>
        <li><span class="pages">16-19</span><span class="section">Bottled water, stubby coolers &amp; car accessories</span></li>
        <li><span class="pages">20-21</span><span class="section">Cooler bags</span></li>
        <li><span class="pages">22-23</span><span class="section">Pens</span></li>
        <li><span class="pages">24-25</span><span class="section">Notebooks &amp; confectionery</span></li>
        <li><span class="pages">26-27</span><span class="section">Drinkware &amp; umbrellas</span></li>
        <li><span class="pages">28-29</span><span class="section">Microfibre cloths &amp; golf</span></li>
        <li><span class="pages">30-33</span><span class="section">Signage &amp; printed sanitiser</span></li>
        <li><span class="pages">34-49</span><span class="section">Product ideas</span></li>
        <li><span class="pages">50</span><span class="section">Cleaning &amp; sanitiser</span></li>
        <li><span class="pages">51</span><span class="section">Stock control</span></li>
      </ol>
      <div class="footer-rule"></div>
      <p class="footer-url">korvane.com.au</p>
    </section>

    <section class="page page-right">
      <svg class="backdrop-shape" width="565" height="790" viewBox="0 0 565 790" aria-hidden="true">
        <defs>
          <linearGradient id="panelBlue" x1="0" y1="0" x2="1" y2="1">
            <stop offset="0" stop-color="#0f3a66"/>
            <stop offset="1" stop-color="#3a74a3"/>
          </linearGradient>
        </defs>
        <path d="M0 118 L 565 118 L 565 790 L 0 790 Z" fill="url(#panelBlue)"/>
      </svg>

      <div class="value-grid">
        <article class="value-card">
          <div class="photo photo-care" role="img" aria-label="Red heart beside a car key"></div>
          <div class="label"><h3>Care</h3><p>Others needs above our own will always result in a win-win.</p></div>
        </article>
        <article class="value-card">
          <div class="photo photo-speed" role="img" aria-label="Red sports car being delivered"></div>
          <div class="label"><h3>Speed</h3><p>Efficiency in everything we do</p></div>
        </article>
        <article class="value-card">
          <div class="photo photo-satisfaction" role="img" aria-label="Luxury car dashboard and steering wheel"></div>
          <div class="label"><h3>Satisfaction</h3><p>Exceeding expectations every time</p></div>
        </article>
        <article class="value-card">
          <div class="photo photo-enjoyment" role="img" aria-label="Red apple wrapped in a measuring tape"></div>
          <div class="label"><h3>Enjoyment</h3><p>All with an element of fun..</p></div>
        </article>
      </div>

      <div class="about">
        <h2>Who we are</h2>
        <p>For over three decades, Korvane has provided complete merchandise solutions for an ever-increasing number of Australian corporations and businesses. During this time, our already vast range has grown exponentially and our systems have become increasingly more streamlined to cope with the sheer volume.</p>
        <p>Our enviable reputation is built on experience, innovation and economies of scale that come with being a major wholesaler in Australia. We pride ourselves on our accountability, efficiency, consistency, instant reporting and above all, the ability to see things from your point of view.</p>
        <p>We love to strategise with you to make sure what we supply will achieve the desired outcome. Every day we see companies giving away merchandise aimlessly and our mission is to supply you with a product that will suit your criteria.</p>
      </div>

      <div class="team-photo" role="img" aria-label="Business team meeting around a table in front of a data screen"></div>
    </section>
  </main>
</body>
</html>
```